I need a flyer made , the flyer can be one page or two pages or three pages . I will be posting this on Instagram and social media platforms. I am a luxury home builder , I am looking to hire a construction project manager . Below are some examples and ideas what can be on the flyer

We’re looking for a construction project manager who’s passionate about building luxury homes at the highest standards
We’re hiring construction project manager
* Experience 5+ years in residential project management with a strong portfolio of completed homes.
* location : Bergen County NJ
* excellent leadership skills, leads teams with confidence and clarity
* communicates seamlessly with architects , engineers, designers and clients
*knows how to manage budgets and timelines without compromising quality
*solves problems with a positive solution first mindset
* pays attention to every detail because in luxury the small things are the big things

Apply now , link in bio or DM to connect.

My logo is attached, my web site www.velstridebuilders.com
My style is modern but still warm and inviting. I like a clean classy look .

Please don’t add any images of chairs or people to the flyer , I do not want people on my flyer. Do not add standard images of offices and houses , we are luxury builders , we build homes over 2 million dollars. Keep a classy , simple modern look . High end .

You can add a white hard hat with my logo on it for a image , this is a suggestion does not have to be on my flyer ,

```html
<!DOCTYPE html>
<html lang="en">
<head>
<meta charset="utf-8">
<title>Hiring – Construction Project Manager – Velstride Builders</title>
<link rel="stylesheet" href="https://fonts.googleapis.com/css2?family=Exo+2:wght@600;700;800&family=Montserrat:wght@400;500&family=Cinzel:wght@400;500&display=swap">
<style>
  :root {
    --ink: #000000;
    --paper: #ffffff;
    --panel-grey: #d9d9d9;
    --megaphone-fill: #2a2a2a;
  }
  html, body {
    margin: 0;
    padding: 0;
    width: 1200px;
    height: 1200px;
    overflow: hidden;
    background: var(--ink);
  }
  .flyer {
    position: relative;
    width: 1200px;
    height: 1200px;
    background: var(--ink);
    color: var(--paper);
    overflow: hidden;
  }
  .flyer-shapes {
    position: absolute;
    inset: 0;
  }
  .headline-small {
    position: absolute;
    left: 174px;
    top: 222px;
    margin: 0;
    font-family: "Exo 2", sans-serif;
    font-weight: 700;
    font-size: 46px;
    line-height: 1;
    letter-spacing: 0.5px;
  }
  .headline-large {
    position: absolute;
    left: 168px;
    top: 270px;
    margin: 0;
    font-family: "Exo 2", sans-serif;
    font-weight: 800;
    font-size: 136px;
    line-height: 1;
    letter-spacing: 2px;
  }
  .job-title {
    position: absolute;
    left: 174px;
    top: 490px;
    margin: 0;
    font-family: "Exo 2", sans-serif;
    font-weight: 700;
    font-size: 38px;
    line-height: 1;
  }
  .requirements-title {
    position: absolute;
    left: 174px;
    top: 615px;
    margin: 0;
    font-family: "Exo 2", sans-serif;
    font-weight: 700;
    font-size: 38px;
    line-height: 1;
  }
  .requirement-list {
    position: absolute;
    margin: 0;
    padding: 0;
    list-style: none;
    font-family: "Montserrat", sans-serif;
    font-size: 16.5px;
    line-height: 26px;
    color: var(--paper);
  }
  .requirement-list--left { left: 168px; top: 684px; width: 420px; }
  .requirement-list--right { left: 612px; top: 686px; width: 495px; }
  .requirement-list li {
    position: relative;
    padding-left: 36px;
    margin-bottom: 16px;
  }
  .requirement-list--right li { margin-bottom: 15px; }
  .requirement-list .tick {
    position: absolute;
    left: 0;
    top: 7px;
    width: 16px;
    height: 16px;
  }
  .apply-button {
    position: absolute;
    left: 881px;
    top: 886px;
    width: 186px;
    height: 61px;
    background: var(--panel-grey);
    color: var(--ink);
    font-family: "Cinzel", serif;
    font-weight: 500;
    font-size: 22px;
    letter-spacing: 1px;
    display: flex;
    align-items: center;
    justify-content: center;
  }
  .brand-name {
    position: absolute;
    left: 700px;
    top: 990px;
    width: 440px;
    margin: 0;
    text-align: center;
    font-family: "Cinzel", serif;
    font-weight: 400;
    font-size: 40px;
    line-height: 1;
    letter-spacing: 1px;
    color: var(--paper);
  }
  .website {
    position: absolute;
    left: 620px;
    top: 1083px;
    width: 506px;
    margin: 0;
    text-align: center;
    font-family: "Montserrat", sans-serif;
    font-weight: 500;
    font-size: 28px;
    line-height: 1;
    letter-spacing: 0.8px;
    color: var(--paper);
  }
</style>
</head>
<body>
<main class="flyer">
  <svg class="flyer-shapes" width="1200" height="1200" viewBox="0 0 1200 1200" aria-hidden="false">
    <!-- speech bubble frame -->
    <path class="speech-frame" d="M128 114 H1089 Q1117 114 1117 142 V892 Q1117 920 1089 920 H689 L326 1138 Q298 1152 298 1122 V920 H126 Q98 920 98 892 V142 Q98 114 128 114 Z"
          fill="none" stroke="var(--paper)" stroke-width="4" stroke-linejoin="round"/>

    <!-- announcement badge -->
    <circle class="announce-ring" cx="1000" cy="236" r="167" fill="var(--ink)" stroke="var(--paper)" stroke-width="4"/>
    <circle class="announce-art" cx="1000" cy="236" r="138" fill="var(--megaphone-fill)" role="img" aria-label="Megaphone with sound bolts announcing the opening"/>

    <!-- side panels -->
    <rect class="side-panel side-panel--left" x="0" y="200" width="113" height="236" fill="var(--panel-grey)"/>
    <rect class="side-panel side-panel--right" x="1097" y="518" width="103" height="236" fill="var(--panel-grey)"/>
    <g class="panel-dots" fill="var(--ink)">
      <circle cx="34" cy="400" r="5"/><circle cx="56" cy="400" r="5"/><circle cx="78" cy="400" r="5"/>
      <circle cx="1127" cy="553" r="5"/><circle cx="1149" cy="553" r="5"/><circle cx="1171" cy="553" r="5"/>
    </g>

    <!-- accent dots -->
    <g class="accent-dots" fill="var(--paper)">
      <circle cx="173" cy="61" r="5"/><circle cx="195" cy="61" r="5"/><circle cx="217" cy="61" r="5"/>
      <circle cx="690" cy="452" r="5"/><circle cx="712" cy="452" r="5"/><circle cx="734" cy="452" r="5"/>
      <circle cx="176" cy="566" r="5"/><circle cx="198" cy="566" r="5"/><circle cx="220" cy="566" r="5"/>
      <circle cx="1028" cy="1136" r="5"/><circle cx="1050" cy="1136" r="5"/><circle cx="1072" cy="1136" r="5"/>
    </g>

    <!-- accent lines -->
    <g class="accent-lines" stroke="var(--paper)" stroke-width="3" stroke-linecap="round">
      <line x1="1112" y1="62" x2="1176" y2="62"/>
      <line x1="1146" y1="72" x2="1200" y2="72" stroke-width="1.5"/>
      <line x1="64" y1="1069" x2="129" y2="1069"/>
      <line x1="97" y1="1079" x2="163" y2="1079" stroke-width="1.5"/>
    </g>
  </svg>

  <p class="headline-small">WE ARE</p>
  <h1 class="headline-large">HIRING!</h1>
  <h2 class="job-title">Construction Project Manager</h2>
  <h3 class="requirements-title">Requirement :</h3>

  <ul class="requirement-list requirement-list--left">
    <li><svg class="tick" viewBox="0 0 16 16"><circle cx="7.5" cy="8.5" r="6" fill="none" stroke="var(--paper)" stroke-width="1.5"/><path d="M4.5 8.5 L7.3 11 L14 3.5" fill="none" stroke="var(--paper)" stroke-width="1.8" stroke-linecap="round" stroke-linejoin="round"/></svg>Experience 5+ Years In Residential Project Management With A Strong Portfolio.</li>
    <li><svg class="tick" viewBox="0 0 16 16"><circle cx="7.5" cy="8.5" r="6" fill="none" stroke="var(--paper)" stroke-width="1.5"/><path d="M4.5 8.5 L7.3 11 L14 3.5" fill="none" stroke="var(--paper)" stroke-width="1.8" stroke-linecap="round" stroke-linejoin="round"/></svg>Location : Bergen County NJ</li>
    <li><svg class="tick" viewBox="0 0 16 16"><circle cx="7.5" cy="8.5" r="6" fill="none" stroke="var(--paper)" stroke-width="1.5"/><path d="M4.5 8.5 L7.3 11 L14 3.5" fill="none" stroke="var(--paper)" stroke-width="1.8" stroke-linecap="round" stroke-linejoin="round"/></svg>Excellent Leadership Skills, Leads Teams With Confidence And Clarity</li>
  </ul>

  <ul class="requirement-list requirement-list--right">
    <li><svg class="tick" viewBox="0 0 16 16"><circle cx="7.5" cy="8.5" r="6" fill="none" stroke="var(--paper)" stroke-width="1.5"/><path d="M4.5 8.5 L7.3 11 L14 3.5" fill="none" stroke="var(--paper)" stroke-width="1.8" stroke-linecap="round" stroke-linejoin="round"/></svg>Communicates Seamlessly With Architects , Engineers, Designers And Clients</li>
    <li><svg class="tick" viewBox="0 0 16 16"><circle cx="7.5" cy="8.5" r="6" fill="none" stroke="var(--paper)" stroke-width="1.5"/><path d="M4.5 8.5 L7.3 11 L14 3.5" fill="none" stroke="var(--paper)" stroke-width="1.8" stroke-linecap="round" stroke-linejoin="round"/></svg>Solves Problems With A Positive Solution First Mindset</li>
    <li><svg class="tick" viewBox="0 0 16 16"><circle cx="7.5" cy="8.5" r="6" fill="none" stroke="var(--paper)" stroke-width="1.5"/><path d="M4.5 8.5 L7.3 11 L14 3.5" fill="none" stroke="var(--paper)" stroke-width="1.8" stroke-linecap="round" stroke-linejoin="round"/></svg>Pays Attention To Every Detail Because In Luxury The Small Things Are The Big Things</li>
  </ul>

  <div class="apply-button">Apply now</div>

  <p class="brand-name">Velstride Builders</p>
  <p class="website">www.velstridebuilders.com</p>
</main>
</body>
</html>
```